Real estate broker business card

Want a modern celan but effective business card for my residential and commercial real estate business. I want the back of the card to advertise my services and to capture business. I have attached the back of my current business card fore ideas
Updates

Logos, photo and text updates added! Added Saturday, September 3, 2016

Project Deadline Extended Reason: LOGOS, PHOTOS AND TEST JUST UPLOADED! I'M READY TO PICK A DESIGN! THANK YOU! Added Saturday, September 3, 2016

Target Market(s)

home buyers and seller. commercial buyers and sellers

Industry/Entity Type

Real Estate

Contact Information for Business Card

must have my contact information and my photo

Requirements
Must have
• Carla Ventrino
• Owner & Qualifying Broker
• Ventrino Real Estate Services
• 505.718.2094
• carla@ventrinohomes.example
• www.ventrinohomes.example
Nice to have
• metallic
• Business capture text: " Don't buy or lease property without someone looking out for your best interests. I will represent you on your home or investment purchase for FREE!"
• "Home owners, call today to receive a FREE market analysis for your homes value!

```html
<!DOCTYPE html>
<html lang="en">
<head>
<meta charset="utf-8">
<title>Carla Ventrino — Business Card</title>
<link rel="stylesheet" href="https://fonts.googleapis.com/css2?family=Cinzel:wght@500;600&family=Fira+Sans+Condensed:wght@400;500&display=swap">
<style>
  :root {
    --backdrop: #1e1e1e;
    --teal-light: #1b8a9a;
    --teal-mid: #116b78;
    --teal-dark: #0a4d58;
    --silver-light: #e9ecee;
    --silver-dark: #8b9196;
    --ink-light: #eef4f5;
    --ink-soft: #d6e4e6;
    --card-white: #ffffff;
    --brand-teal: #17707d;
    --photo-dark: #2c3a27;
    --photo-mid: #6b5648;
    --photo-light: #c9b6a6;
  }
  * { box-sizing: border-box; margin: 0; padding: 0; }
  html, body { width: 1200px; height: 987px; overflow: hidden; }
  body { background: var(--backdrop); position: relative; }

  .card {
    position: absolute;
    left: 293px;
    width: 615px;
    height: 352px;
    overflow: hidden;
    box-shadow: 0 6px 18px rgba(0,0,0,.45);
  }
  .card--front { top: 130px; display: flex; }
  .card--back { top: 505px; background: var(--card-white); }

  .portrait {
    width: 300px;
    height: 100%;
    background:
      radial-gradient(ellipse 55% 60% at 48% 42%, var(--photo-light) 0%, var(--photo-mid) 45%, transparent 75%),
      linear-gradient(160deg, var(--photo-dark), #1f2a1c);
  }

  .info-panel {
    width: 300px;
    height: 100%;
    background: radial-gradient(ellipse 90% 80% at 60% 35%, var(--teal-light) 0%, var(--teal-mid) 55%, var(--teal-dark) 100%);
    padding: 56px 0 0 33px;
    color: var(--ink-light);
  }
  .metal-strip {
    width: 15px;
    height: 100%;
    background: linear-gradient(90deg, var(--silver-dark), var(--silver-light) 45%, var(--silver-dark));
  }

  .agent-name {
    font-family: "Cinzel", serif;
    font-weight: 500;
    font-size: 23px;
    letter-spacing: .5px;
    line-height: 1;
    margin-bottom: 8px;
  }
  .agent-role {
    font-family: "Fira Sans Condensed", sans-serif;
    font-size: 15.5px;
    text-transform: uppercase;
    line-height: 21px;
    color: var(--ink-soft);
  }
  .contact-list {
    list-style: none;
    margin-top: 20px;
    font-family: "Fira Sans Condensed", sans-serif;
    font-size: 15.5px;
    text-transform: uppercase;
    color: var(--ink-light);
  }
  .contact-list li {
    display: flex;
    align-items: center;
    gap: 8px;
    height: 23.5px;
  }
  .contact-list svg { width: 14px; height: 14px; flex: none; fill: var(--ink-light); }
  .capture-text {
    margin-top: 24px;
    font-family: "Fira Sans Condensed", sans-serif;
    font-size: 15.5px;
    text-transform: uppercase;
    line-height: 22.5px;
    color: var(--ink-light);
  }

  .brand-lockup {
    position: absolute;
    left: 50%;
    top: 175px;
    transform: translate(-50%, -50%);
    display: flex;
    align-items: center;
    gap: 14px;
  }
  .brand-mark {
    width: 26px;
    height: 26px;
    background: var(--brand-teal);
  }
  .brand-name {
    font-family: "Cinzel", serif;
    font-weight: 600;
    font-size: 26px;
    color: var(--brand-teal);
    white-space: nowrap;
  }
</style>
</head>
<body>
  <section class="card card--front">
    <div class="portrait" role="img" aria-label="Portrait photo of Carla Ventrino against a green outdoor background"></div>
    <div class="info-panel">
      <h1 class="agent-name">Carla Ventrino</h1>
      <p class="agent-role">Owner &amp; Qualifying Broker<br>Ventrino Real Estate Services</p>
      <ul class="contact-list">
        <li>
          <svg viewBox="0 0 24 24" aria-hidden="true"><path d="M6.6 10.8a15.2 15.2 0 0 0 6.6 6.6l2.2-2.2c.3-.3.7-.4 1-.2 1.1.4 2.3.6 3.6.6.6 0 1 .4 1 1V20c0 .6-.4 1-1 1A17 17 0 0 1 3 4c0-.6.4-1 1-1h3.5c.6 0 1 .4 1 1 0 1.3.2 2.5.6 3.6.1.3 0 .7-.2 1z"/></svg>
          505.718.2094
        </li>
        <li>
          <svg viewBox="0 0 24 24" aria-hidden="true"><path d="M2 5h20v14H2z" fill="none"/><path d="M2 5h20v14H2V5zm2 2v.5l8 5 8-5V7H4zm0 2.9V17h16V9.9l-8 5-8-5z"/></svg>
          carla@ventrinohomes.example
        </li>
        <li>
          <svg viewBox="0 0 24 24" aria-hidden="true"><path d="M12 2a10 10 0 1 0 0 20 10 10 0 0 0 0-20zm6.9 6h-2.9a15.7 15.7 0 0 0-1.4-3.6A8 8 0 0 1 18.9 8zM12 4c.8 1.2 1.5 2.5 1.9 4h-3.8c.4-1.5 1.1-2.8 1.9-4zM4.3 14a8.2 8.2 0 0 1 0-4h3.4a16.5 16.5 0 0 0 0 4H4.3zm.8 2h2.9c.3 1.3.8 2.5 1.4 3.6A8 8 0 0 1 5.1 16zM8 8H5.1a8 8 0 0 1 4.3-3.6C8.8 5.5 8.3 6.7 8 8zm4 12c-.8-1.2-1.5-2.5-1.9-4h3.8c-.4 1.5-1.1 2.8-1.9 4zm2.3-6H9.7a14.7 14.7 0 0 1 0-4h4.6a14.7 14.7 0 0 1 0 4zm.3 5.6c.6-1.1 1.1-2.3 1.4-3.6h2.9a8 8 0 0 1-4.3 3.6zm1.7-5.6a16.5 16.5 0 0 0 0-4h3.4a8.2 8.2 0 0 1 0 4h-3.4z"/></svg>
          www.ventrinohomes.example
        </li>
      </ul>
      <p class="capture-text">Home owners, call today to<br>receive a free market analysis<br>for your homes value!</p>
    </div>
    <div class="metal-strip"></div>
  </section>

  <section class="card card--back">
    <div class="brand-lockup">
      <span class="brand-mark"></span>
      <span class="brand-name">Ventrino Real Estate Services</span>
    </div>
  </section>
</body>
</html>
```